Lucky Pearl Dumpling Kitchen - Website Design - Food Manufacturer of Yum Cha Style Finger Foods

Need a modern and fresh redesign of our existing website (www.luckypearldumpling.com.au).
We are a Sydney based Dim Sim manufacturer since 1982, and we make all sorts of Yum cha products and distribute nationally.
I am looking for a modern take, more funky than formal.
The final design should communicate premium quality authentic product manufactured LOCALLY and NOT imported.

```html
<!DOCTYPE html>
<html lang="en">
<head>
<meta charset="utf-8">
<title>Lucky Pearl Dumpling Kitchen</title>
<link href="https://fonts.googleapis.com/css2?family=Roboto:wght@400;500;700&display=swap" rel="stylesheet">
<style>
:root{
  --red:#ee3a32;
  --ink:#231f20;
  --text:#444;
  --muted:#666;
  --grey-band:#f3f2f2;
  --footer:#454545;
  --white:#fff;
  --line:#c9c9c9;
  --photo-warm:#b88a52;
  --photo-dark:#4a2e22;
}
*{margin:0;padding:0;box-sizing:border-box}
html,body{width:689px;height:1200px;overflow:hidden;background:var(--white)}
body{position:relative;font-family:"Roboto",Arial,sans-serif;color:var(--text)}
.abs{position:absolute}

/* header */
.brand{left:74px;top:16px;display:flex;align-items:center;gap:6px}
.brand-mark{width:14px;height:14px;background:var(--red)}
.brand-name{font-size:10px;font-weight:500;color:var(--ink);width:96px;line-height:12px}
.cart{left:538px;top:15px;display:flex;align-items:center;gap:6px;font-size:7px;color:var(--muted)}
.cart b{font-weight:400;color:var(--red)}
.search{left:492px;top:39px;width:121px;height:20px;background:#f0eeee;border:0}
.search-btn{left:593px;top:39px;width:20px;height:20px;background:var(--red)}

/* nav */
.nav{left:0;top:74px;width:689px;height:26px;background:var(--ink)}
.nav a{position:absolute;top:0;height:26px;line-height:26px;font-size:7.5px;color:var(--white);text-decoration:none}
.nav .active{background:var(--red);width:53px;text-align:center}

/* hero */
.hero{left:74px;top:112px;width:540px;height:236px;background:linear-gradient(120deg,var(--photo-dark) 0%,#6b4630 35%,var(--photo-warm) 60%,#d6b27a 80%,#5a3a28 100%)}
.hero-arrow{top:219px;width:26px;height:25px;background:rgba(255,255,255,.35)}

/* welcome */
.welcome-title{left:0;top:376px;width:689px;text-align:center;font-size:14.5px;font-weight:500;color:var(--ink)}
.welcome-title span{color:var(--red)}
.welcome-copy{left:90px;top:406px;width:509px;text-align:center;font-size:7px;line-height:14.5px;color:var(--muted)}
.btn-read{left:311px;top:458px;width:66px;height:19px;background:var(--red);color:var(--white);font-size:7.5px;text-align:center;line-height:19px}

/* featured */
.featured{left:0;top:494px;width:689px;height:256px;background:var(--grey-band)}
.featured-title{left:0;top:517px;width:689px;text-align:center;font-size:14px;font-weight:500;color:var(--ink)}
.card{top:547px;width:126px;height:177px;background:var(--red);color:var(--white);text-align:center}
.card-photo{position:absolute;left:9px;top:10px;width:108px;height:71px;border:2px solid var(--white)}
.card-name{position:absolute;left:0;top:96px;width:126px;font-size:9px;font-weight:500}
.card-desc{position:absolute;left:10px;top:114px;width:106px;font-size:6.8px;line-height:11.5px}
.card-price{position:absolute;left:10px;top:152px;font-size:10.5px;font-weight:500}
.card-add{position:absolute;left:70px;top:150px;width:46px;height:16px;background:var(--ink);font-size:6.5px;line-height:16px}
.carousel-next{left:664px;top:620px;width:25px;height:25px;background:#dcdcdc}

/* awards */
.awards-title{left:0;top:780px;width:689px;text-align:center;font-size:12.5px;line-height:20px;color:var(--ink)}
.awards-title span{color:var(--red)}
.award-photo{top:845px;height:108px}

/* sponsors */
.tier{font-size:6px;font-style:italic;font-weight:500;color:#555}
.badge{height:20px;background:#d8d8d8;border-radius:3px}
.badge.sm{height:14px;background:#e2e2e2}
.rule{background:var(--line)}

/* footer */
.footer{left:0;top:1151px;width:689px;height:49px;background:var(--footer)}
.copyright{left:76px;top:1173px;font-size:7px;color:var(--white)}
.social{top:1169px;width:17px;height:17px;border-radius:50%;background:var(--white)}
</style>
</head>
<body>

<header>
  <div class="abs brand"><span class="brand-mark"></span><span class="brand-name">Lucky Pearl Dumpling Kitchen</span></div>
  <div class="abs cart">
    <svg width="13" height="12" viewBox="0 0 13 12"><path d="M1 4h11l-1.5 7h-8z" fill="#666"/><path d="M4 4l2-3M9 4L7 1" stroke="#666" fill="none"/></svg>
    My Cart <b>(0) Item</b>
  </div>
  <div class="abs search"></div>
  <div class="abs search-btn">
    <svg width="20" height="20" viewBox="0 0 20 20"><circle cx="9" cy="9" r="3" stroke="#fff" stroke-width="1.3" fill="none"/><path d="M11.2 11.2l2.5 2.5" stroke="#fff" stroke-width="1.5"/></svg>
  </div>
</header>

<nav class="abs nav">
  <a class="active" style="left:74px">Home</a>
  <a style="left:145px">About Us</a>
  <a style="left:206px">Products</a>
  <a style="left:266px">Promotions</a>
  <a style="left:340px">Contact Us</a>
  <a style="left:412px">Download Our Brouchers</a>
</nav>

<section>
  <div class="abs hero" role="img" aria-label="Steamed buns in a bamboo steamer with chopsticks, soy sauce and coriander"></div>
  <div class="abs hero-arrow" style="left:74px"><svg width="26" height="25"><path d="M15 8l-4 4.5 4 4.5" stroke="#222" fill="none" stroke-width="1.3"/></svg></div>
  <div class="abs hero-arrow" style="left:588px"><svg width="26" height="25"><path d="M11 8l4 4.5-4 4.5" stroke="#222" fill="none" stroke-width="1.3"/></svg></div>
</section>

<section>
  <h1 class="abs welcome-title">Welcome to <span>Lucky Pearl Dumpling</span> Kitchen!</h1>
  <p class="abs welcome-copy">Established in 1982 by Master Chef Lam Wai Ming, Lucky Pearl Dumpling Kitchen has grown from a small family business to a mass manufacturer and distributor of oriental finger food delicacies across Australia. With over 27 years of experience from our master chefs, our company endeavors to provide a range of traditional and contemporary Asian products to meet all sorts of tastes.</p>
  <div class="abs btn-read">Read More</div>
</section>

<section>
  <div class="abs featured"></div>
  <h2 class="abs featured-title">Featured Products</h2>

  <div class="abs card" style="left:74px">
    <div class="card-photo" role="img" aria-label="Dumplings in a bamboo steamer with fresh vegetables" style="background:linear-gradient(135deg,#c79a4e,#e6d6a8 55%,#6a8a3a)"></div>
    <div class="card-name">Product Name</div>
    <div class="card-desc">Neque porro quisquam est qui dolorem ipsum sit.</div>
    <div class="card-price">$22.00</div>
    <div class="card-add">Add to Cart</div>
  </div>
  <div class="abs card" style="left:212px">
    <div class="card-photo" role="img" aria-label="Packet of barbecue pork buns" style="background:linear-gradient(180deg,#2c2c3a,#5a5f78 55%,#e8e0cc)"></div>
    <div class="card-name">Product Name</div>
    <div class="card-desc">Neque porro quisquam est qui dolorem ipsum sit.</div>
    <div class="card-price">$22.00</div>
    <div class="card-add">Add to Cart</div>
  </div>
  <div class="abs card" style="left:350px">
    <div class="card-photo" role="img" aria-label="Packet of pork dim sims" style="background:linear-gradient(180deg,#2c2c3a,#5a6078 55%,#e0b94a)"></div>
    <div class="card-name">Product Name</div>
    <div class="card-desc">Neque porro quisquam est qui dolorem ipsum sit.</div>
    <div class="card-price">$22.00</div>
    <div class="card-add">Add to Cart</div>
  </div>
  <div class="abs card" style="left:488px">
    <div class="card-photo" role="img" aria-label="Two customers holding a product pack" style="background:linear-gradient(180deg,#c8b89c,#8a7a66 60%,#5b5550)"></div>
    <div class="card-name">Product Name</div>
    <div class="card-desc">Neque porro quisquam est qui dolorem ipsum sit.</div>
    <div class="card-price">$22.00</div>
    <div class="card-add">Add to Cart</div>
  </div>
  <div class="abs carousel-next"><svg width="25" height="25"><path d="M11 8l4 4.5-4 4.5" stroke="#fff" fill="none" stroke-width="1.3"/></svg></div>
</section>

<section>
  <h2 class="abs awards-title">2009 PCBA AWARDS SMALL MEDIUM ENTERPRISE WINNER<br><span>AND</span> 2009 HARBOUR CITY SUCCESS STORY WINNER</h2>
  <div class="abs award-photo" style="left:77px;width:121px;background:linear-gradient(90deg,#5a2a30,#8a6a70 50%,#c8ccd4)" role="img" aria-label="Award winners receiving a trophy on stage"></div>
  <div class="abs award-photo" style="left:215px;width:121px;background:linear-gradient(90deg,#3a4a3a,#8a7a78 50%,#6a2a44)" role="img" aria-label="Two men holding an award certificate"></div>
  <div class="abs award-photo" style="left:354px;width:116px;background:linear-gradient(90deg,#d26a3a,#8a7a78 50%,#b8a890)" role="img" aria-label="Award presentation with certificate"></div>
  <div class="abs award-photo" style="left:494px;width:111px;height:114px;background:linear-gradient(180deg,#ffffff 0%,#f6f6f6 45%,#e23a12 46%,#e03a10 100%)" role="img" aria-label="Success story award poster"></div>
</section>

<section>
  <div class="abs tier" style="left:82px;top:993px">Platinum Sponsors</div>
  <div class="abs badge" style="left:82px;top:1006px;width:118px"></div>
  <div class="abs badge" style="left:234px;top:1006px;width:52px"></div>
  <div class="abs badge" style="left:312px;top:1006px;width:114px"></div>
  <div class="abs badge" style="left:457px;top:1006px;width:68px"></div>
  <div class="abs badge" style="left:558px;top:1003px;width:32px;height:30px;border-radius:50%"></div>
  <div class="abs rule" style="left:82px;top:1036px;width:519px;height:1px"></div>

  <div class="abs tier" style="left:82px;top:1040px">Major Event Sponsors</div>
  <div class="abs badge" style="left:86px;top:1052px;width:44px;height:24px"></div>
  <div class="abs badge" style="left:160px;top:1052px;width:34px;height:24px"></div>
  <div class="abs badge" style="left:226px;top:1052px;width:44px;height:24px"></div>
  <div class="abs badge sm" style="left:296px;top:1058px;width:70px"></div>
  <div class="abs badge sm" style="left:388px;top:1058px;width:94px"></div>
  <div class="abs rule" style="left:499px;top:1040px;width:1px;height:72px"></div>
  <div class="abs tier" style="left:511px;top:1063px">Event Supporters</div>
  <div class="abs badge" style="left:511px;top:1076px;width:22px;height:18px"></div>
  <div class="abs badge" style="left:542px;top:1076px;width:30px;height:18px"></div>
  <div class="abs badge" style="left:580px;top:1076px;width:20px;height:18px"></div>
  <div class="abs badge sm" style="left:513px;top:1101px;width:54px;height:9px"></div>

  <div class="abs tier" style="left:82px;top:1088px">Event Sponsors</div>
  <div class="abs badge sm" style="left:82px;top:1098px;width:32px"></div>
  <div class="abs badge sm" style="left:130px;top:1098px;width:18px;border-radius:50%;height:18px"></div>
  <div class="abs badge sm" style="left:164px;top:1098px;width:62px"></div>
  <div class="abs badge sm" style="left:242px;top:1098px;width:44px"></div>
  <div class="abs badge sm" style="left:306px;top:1098px;width:24px"></div>
  <div class="abs badge sm" style="left:350px;top:1098px;width:68px"></div>
  <div class="abs badge sm" style="left:428px;top:1098px;width:56px"></div>
</section>

<footer>
  <div class="abs footer"></div>
  <div class="abs copyright">Copyright © 2014 Yoursite. All rights reserved.</div>
  <div class="abs social" style="left:514px"></div>
  <div class="abs social" style="left:535px"></div>
  <div class="abs social" style="left:556px"></div>
  <div class="abs social" style="left:577px"></div>
  <div class="abs social" style="left:598px"></div>
</footer>

</body>
</html>
```